New business card/stationary for a consulting company

I am looking for a clean and very professional looking business card for my consulting company as well as corresponding stationary. I am uploading our logo. I like simple and powerful for the feel. No graphics but I am open on everything else. Below is my contact information but would like the final to be in a version I can add my employees information into and print. Thank you.

Daniel Whitcombe
dan@ferncliffadvisory.com
2870 North 9th Avenue, Summit Floor, Elm Ridge, Illinois 60531
www.ferncliffadvisory.com

Industry/Entity Type

Consulting

Contact Information for Business Card

Daniel Whitcombe
dan@ferncliffadvisory.com
www.ferncliffadvisory.com

Font styles to use
Serif
Sans Serif

Requirements
Must have
• Our logo and the business card details.
Nice to have
• our website www.ferncliffadvisory.com

```html
<!DOCTYPE html>
<html lang="en">
<head>
<meta charset="utf-8">
<title>Ferncliff Advisory – Business Card</title>
<link href="https://fonts.googleapis.com/css2?family=Open+Sans:wght@400;700&display=swap" rel="stylesheet">
<style>
  :root {
    --navy: #17176b;
    --text-grey: #6b6b6b;
    --rule-grey: #9a9a9a;
    --card: #fbfbfb;
    --backdrop: #e6e6e6;
  }
  * { margin: 0; padding: 0; box-sizing: border-box; }
  html, body { width: 1200px; height: 904px; overflow: hidden; }
  body {
    background: var(--backdrop);
    font-family: "Open Sans", sans-serif;
    position: relative;
  }
  .card {
    position: absolute;
    width: 630px;
    height: 360px;
    background: var(--card);
    box-shadow: 0 2px 10px rgba(0,0,0,0.12);
  }
  .card--back { left: 285px; top: 62px; }
  .card--front { left: 285px; top: 482px; }

  .brand {
    position: absolute;
    left: 0; right: 0;
    display: flex;
    justify-content: center;
    align-items: center;
    gap: 12px;
    color: var(--navy);
    font-weight: 400;
    letter-spacing: 0.12em;
    text-transform: uppercase;
  }
  .brand__mark { width: 18px; height: 18px; background: var(--navy); }
  .card--back .brand { top: 160px; font-size: 24px; }
  .card--front .brand { top: 48px; font-size: 26px; }

  .holder {
    position: absolute;
    left: 70px;
    top: 196px;
    color: var(--navy);
    font-weight: 700;
    font-size: 19px;
  }
  .divider {
    position: absolute;
    left: 300px;
    top: 130px;
    width: 1px;
    height: 116px;
    background: var(--rule-grey);
  }
  .contact {
    position: absolute;
    left: 328px;
    top: 128px;
    color: var(--text-grey);
    font-size: 14.5px;
    line-height: 23px;
    list-style: none;
  }
  .contact__item { display: flex; align-items: center; gap: 8px; }
  .contact__item svg { width: 15px; height: 15px; flex: none; }
  .band {
    position: absolute;
    left: 0; right: 0;
    bottom: 30px;
    height: 5px;
    background: var(--navy);
  }
</style>
</head>
<body>
  <section class="card card--back" aria-label="Card back">
    <div class="brand"><span class="brand__mark"></span>Ferncliff Advisory</div>
  </section>

  <section class="card card--front" aria-label="Card front">
    <div class="brand"><span class="brand__mark"></span>Ferncliff Advisory</div>
    <p class="holder">Daniel Whitcombe</p>
    <div class="divider"></div>
    <ul class="contact">
      <li>2870 North 9th Avenue</li>
      <li>Summit Floor, Elm Ridge</li>
      <li>Illinois 60531</li>
      <li class="contact__item">
        <svg viewBox="0 0 16 16" aria-hidden="true"><rect x="1" y="3" width="14" height="10" rx="1.5" fill="var(--navy)"/><path d="M1.5 4 8 9l6.5-5" stroke="#fff" stroke-width="1.4" fill="none"/></svg>
        dan@ferncliffadvisory.com
      </li>
      <li class="contact__item">
        <svg viewBox="0 0 16 16" aria-hidden="true"><circle cx="8" cy="8" r="7" fill="var(--navy)"/><g stroke="#fff" stroke-width="1" fill="none"><ellipse cx="8" cy="8" rx="3" ry="7"/><path d="M1 8h14M2.5 4.5h11M2.5 11.5h11"/></g></svg>
        www.ferncliffadvisory.com
      </li>
    </ul>
    <div class="band"></div>
  </section>
</body>
</html>
```